iPhone iOS 7 App For Managing Tasks/Photos for Internal Company Use

We need an app design that displays company objectives and task, and provides the interface for employees to complete a task by uploading a photo and adding comments.

Please see attached mock up sketches as a rough guideline

Final delivery of files must contain PSD, and all layers/objects sliced both is PSD and PNG files

Target Market(s)

This is a tool for internal employee use

Industry/Entity Type

It Company

Requirements
Must have
• Must include logo, and match the colour scheme
Use iPhone iOS 7 Style

```html
<!DOCTYPE html>
<html lang="en">
<head>
<meta charset="utf-8">
<title>My Progress</title>
<link href="https://fonts.googleapis.com/css2?family=Arimo:wght@400;700&display=swap" rel="stylesheet">
<style>
  :root {
    --bg-deep: #0b2a3f;
    --bg-mid: #1f5a78;
    --bg-light: #3f8aa8;
    --bar-top: #3a3a3a;
    --bar-bottom: #0e0e0e;
    --text-white: #ffffff;
    --text-blue: #b9e2f7;
    --accent-blue: #22a6ef;
    --accent-deep: #0b3d66;
    --dial-outer: #2b2b2b;
    --dial-track: #3c3c3c;
    --dial-tick: #6a6a6a;
    --dial-face: #c9c9c9;
    --tab-top: #2a2a2a;
    --tab-bottom: #070707;
    --home-orange: #f07a10;
    --target-dark: #3a1410;
    --target-red: #c8281e;
    --news-navy: #1c2c7a;
    --news-paper: #dfe6f2;
    --news-globe: #2d7bd6;
    --logout-red: #e0261e;
  }
  * { margin: 0; padding: 0; box-sizing: border-box; }
  html, body { width: 800px; height: 1200px; overflow: hidden; background: var(--bg-deep); }
  body { font-family: "Arimo", sans-serif; color: var(--text-white); }
  .screen { position: relative; width: 800px; height: 1200px; overflow: hidden; }
  .backdrop {
    position: absolute; inset: 0;
    background: radial-gradient(ellipse at 50% 35%, var(--bg-light) 0%, var(--bg-mid) 40%, var(--bg-deep) 100%);
  }
  .status-bar {
    position: absolute; top: 0; left: 0; width: 800px; height: 50px;
    background: linear-gradient(var(--bar-top), var(--bar-bottom));
    display: flex; align-items: center; justify-content: center;
  }
  .status-time { font-size: 34px; font-weight: 400; line-height: 1; }
  .status-signal { position: absolute; left: 12px; top: 12px; }
  .status-battery { position: absolute; right: 12px; top: 14px; }
  .page-title {
    position: absolute; top: 232px; width: 100%; text-align: center;
    font-size: 42px; font-weight: 700; line-height: 1.2;
  }
  .progress-dial { position: absolute; left: 192px; top: 330px; }
  .progress-caption {
    position: absolute; top: 794px; width: 100%; text-align: center;
    font-size: 29px; font-weight: 700; color: var(--text-blue); line-height: 1.2;
  }
  .tab-bar {
    position: absolute; left: 0; bottom: 0; width: 800px; height: 155px;
    background: linear-gradient(var(--tab-top), var(--tab-bottom));
    display: flex; justify-content: space-around; padding: 0 18px;
  }
  .tab { width: 170px; display: flex; flex-direction: column; align-items: center; padding-top: 15px; }
  .tab-icon { width: 90px; height: 90px; display: block; }
  .tab-label { margin-top: 12px; font-size: 28px; font-weight: 700; line-height: 1.2; }
</style>
</head>
<body>
<div class="screen">
  <div class="backdrop" role="img" aria-label="Rain drops on dark blue glass background"></div>

  <div class="status-bar">
    <svg class="status-signal" width="60" height="26" viewBox="0 0 60 26">
      <rect x="0" y="18" width="8" height="8" fill="#fff"/>
      <rect x="11" y="14" width="8" height="12" fill="#fff"/>
      <rect x="22" y="10" width="8" height="16" fill="#fff"/>
      <rect x="33" y="5" width="8" height="21" fill="#fff"/>
      <rect x="44" y="0" width="8" height="26" fill="#fff"/>
    </svg>
    <span class="status-time">9:20 AM</span>
    <svg class="status-battery" width="56" height="24" viewBox="0 0 56 24">
      <rect x="1" y="1" width="48" height="22" rx="3" fill="none" stroke="#fff" stroke-width="2"/>
      <rect x="4" y="4" width="42" height="16" fill="#fff"/>
      <rect x="50" y="7" width="5" height="10" fill="#fff"/>
    </svg>
  </div>

  <h1 class="page-title">My Progress</h1>

  <svg class="progress-dial" width="400" height="400" viewBox="0 0 400 400" role="img" aria-label="Progress ring at 35 percent">
    <circle cx="200" cy="200" r="198" fill="var(--dial-outer)"/>
    <circle cx="200" cy="200" r="182" fill="none" stroke="var(--dial-tick)" stroke-width="12" stroke-dasharray="2 17.05"/>
    <circle cx="200" cy="200" r="152" fill="none" stroke="var(--dial-track)" stroke-width="32"/>
    <circle cx="200" cy="200" r="152" fill="none" stroke="var(--accent-blue)" stroke-width="32"
            stroke-dasharray="334 621" transform="rotate(-90 200 200)"/>
    <circle cx="200" cy="200" r="128" fill="var(--dial-outer)"/>
    <circle cx="200" cy="200" r="114" fill="var(--dial-face)"/>
    <circle cx="200" cy="200" r="32" fill="var(--accent-blue)" stroke="var(--accent-deep)" stroke-width="2"/>
    <text x="200" y="209" text-anchor="middle" font-family="Arimo, sans-serif" font-size="24" font-weight="700" fill="var(--accent-deep)">35%</text>
  </svg>

  <p class="progress-caption">7/20 Objectives Complete</p>

  <nav class="tab-bar">
    <div class="tab">
      <svg class="tab-icon" viewBox="0 0 90 90">
        <rect width="90" height="90" rx="14" fill="var(--home-orange)"/>
        <path d="M45 18 L72 44 L64 44 L64 70 L52 70 L52 54 L38 54 L38 70 L26 70 L26 44 L18 44 Z" fill="#fff"/>
      </svg>
      <span class="tab-label">Home</span>
    </div>
    <div class="tab">
      <svg class="tab-icon" viewBox="0 0 90 90">
        <rect width="90" height="90" rx="14" fill="var(--target-dark)"/>
        <circle cx="45" cy="47" r="30" fill="var(--target-red)"/>
        <circle cx="45" cy="47" r="21" fill="#fff"/>
        <circle cx="45" cy="47" r="13" fill="var(--target-red)"/>
        <circle cx="45" cy="47" r="5" fill="#fff"/>
      </svg>
      <span class="tab-label">Objective</span>
    </div>
    <div class="tab">
      <svg class="tab-icon" viewBox="0 0 90 90">
        <rect width="90" height="90" rx="14" fill="var(--news-navy)"/>
        <rect x="10" y="10" width="70" height="70" rx="8" fill="var(--news-paper)"/>
        <circle cx="45" cy="40" r="22" fill="var(--news-globe)"/>
        <ellipse cx="45" cy="40" rx="10" ry="22" fill="none" stroke="#fff" stroke-width="2"/>
        <line x1="23" y1="40" x2="67" y2="40" stroke="#fff" stroke-width="2"/>
        <text x="45" y="74" text-anchor="middle" font-family="Arimo, sans-serif" font-size="10" fill="var(--news-navy)">News</text>
      </svg>
      <span class="tab-label">News</span>
    </div>
    <div class="tab">
      <svg class="tab-icon" viewBox="0 0 90 90">
        <rect width="90" height="90" rx="14" fill="var(--logout-red)"/>
        <path d="M31 30 A22 22 0 1 0 59 30" fill="none" stroke="#fff" stroke-width="7" stroke-linecap="round"/>
        <line x1="45" y1="18" x2="45" y2="46" stroke="#fff" stroke-width="7" stroke-linecap="round"/>
      </svg>
      <span class="tab-label">Logout</span>
    </div>
  </nav>
</div>
</body>
</html>
```